Business Card Design Project

We need a business card design for a company based in San Diego California named "TKLMasonry Inc." We are dedicated installers of fireplaces, pre cast concrete, stone masonry. We also pecialice in block construction.
Updates

Thank you very much guys, very good designs so far although I would like to point out that the front should have: Company name, license number, and please tell me if a Qr code is too much (if it isn't then it should be in a bottom corner. <img src="http://qr.pontebo-demo.com/?l=1&s=8&d=BEGIN:VCARD%0AVERSION:2.1%0AN:Elizondo;Tomas+%0AFN:Tomas++Elizondo%0ATEL;WORK;VOICE:19495550134%0AEMAIL;WORK;INTERNET:tklmasonry%40mailbox-demo.com%0AURL:www.tklmasonry-demo.com%0AORG:TKL+Masonry+Inc%0ATITLE:Contractor%0AADR;WORK:;;;Oceanside;California;91734;USA%0AEND:VCARD" alt="QRCode"/>  Or I'll upload the picture.

Also we are currently constructing our website, there you can find pictures of what we do. 
tklmasonry-demo.com 
Thank you guys again.

Industry/Entity Type

Business

Requirements
Must have
• Company name: T K L Masonry Inc
Licence number: 482915
Tomas Elizondo Vega
Phone number: 8410 555 0199
Nice to have
• We would like to have an image that represents the business area of work; a fireplace, a fountain, a balcony, a niche, an arch.

```html
<!DOCTYPE html>
<html lang="en">
<head>
<meta charset="utf-8">
<title>T K L Masonry Inc. — Business Card</title>
<link rel="stylesheet" href="https://fonts.googleapis.com/css2?family=Cinzel:wght@400&family=Open+Sans:wght@400&display=swap">
<style>
  :root {
    --page-bg: #ffffff;
    --card-bg: #232323;
    --ink: #f4f4f4;
    --ink-soft: #cfcfcf;
    --ornament-fill: #8a8a8a;
  }
  html, body {
    margin: 0;
    padding: 0;
    width: 1200px;
    height: 900px;
    overflow: hidden;
    background: var(--page-bg);
  }
  .canvas {
    position: relative;
    width: 1200px;
    height: 900px;
  }
  .business-card {
    position: absolute;
    left: 103px;
    top: 171px;
    width: 1006px;
    height: 574px;
    background: var(--card-bg);
  }
  .corner-frames {
    position: absolute;
    left: 0;
    top: 0;
  }
  .frame-line {
    stroke: var(--ink);
    stroke-width: 2;
    fill: none;
  }
  .frame-dot {
    fill: var(--ink);
  }
  .corner-ornament {
    fill: var(--ornament-fill);
    opacity: 0.55;
  }
  .company-name {
    position: absolute;
    left: 0;
    right: 0;
    top: 251px;
    margin: 0;
    text-align: center;
    font-family: "Cinzel", serif;
    font-weight: 400;
    font-size: 43px;
    letter-spacing: 0.1em;
    text-transform: uppercase;
    color: var(--ink);
    line-height: 1;
    padding-left: 8px;
  }
  .website {
    position: absolute;
    left: 0;
    right: 0;
    top: 308px;
    margin: 0;
    text-align: center;
    font-family: "Open Sans", sans-serif;
    font-size: 19px;
    letter-spacing: 0.03em;
    color: var(--ink);
    line-height: 1;
  }
  .contact-details {
    position: absolute;
    left: 0;
    right: 0;
    top: 408px;
    margin: 0;
    text-align: center;
    font-family: "Open Sans", sans-serif;
    font-size: 15px;
    letter-spacing: 0.04em;
    color: var(--ink-soft);
    line-height: 26px;
  }
  .contact-details span {
    display: block;
  }
</style>
</head>
<body>
<main class="canvas">
  <section class="business-card">
    <svg class="corner-frames" width="1006" height="574" viewBox="0 0 1006 574">
      <rect class="corner-ornament" x="15" y="13" width="54" height="56" rx="10" role="img" aria-label="ornamental corner flourish"/>
      <line class="frame-line" x1="62" y1="36" x2="178" y2="36"/>
      <circle class="frame-dot" cx="178" cy="36" r="3.5"/>
      <line class="frame-line" x1="37" y1="64" x2="37" y2="177"/>
      <circle class="frame-dot" cx="37" cy="177" r="3.5"/>

      <rect class="corner-ornament" x="937" y="13" width="54" height="56" rx="10" role="img" aria-label="ornamental corner flourish"/>
      <line class="frame-line" x1="829" y1="36" x2="944" y2="36"/>
      <circle class="frame-dot" cx="829" cy="36" r="3.5"/>
      <line class="frame-line" x1="969" y1="64" x2="969" y2="177"/>
      <circle class="frame-dot" cx="969" cy="177" r="3.5"/>

      <rect class="corner-ornament" x="15" y="503" width="54" height="56" rx="10" role="img" aria-label="ornamental corner flourish"/>
      <line class="frame-line" x1="38" y1="397" x2="38" y2="510"/>
      <circle class="frame-dot" cx="38" cy="397" r="3.5"/>
      <line class="frame-line" x1="64" y1="537" x2="179" y2="537"/>
      <circle class="frame-dot" cx="179" cy="537" r="3.5"/>

      <rect class="corner-ornament" x="937" y="503" width="54" height="56" rx="10" role="img" aria-label="ornamental corner flourish"/>
      <line class="frame-line" x1="971" y1="397" x2="971" y2="510"/>
      <circle class="frame-dot" cx="971" cy="397" r="3.5"/>
      <line class="frame-line" x1="831" y1="538" x2="944" y2="538"/>
      <circle class="frame-dot" cx="831" cy="538" r="3.5"/>
    </svg>

    <h1 class="company-name">T K L Masonry Inc.</h1>
    <p class="website">www.tklmasonry-demo.com</p>
    <p class="contact-details">
      <span class="contact-name">Tomas Elizondo Vega &middot; 8410 555 0199</span>
      <span class="licence-number">Licence No. 482915</span>
    </p>
  </section>
</main>
</body>
</html>
```